Boutique custom software development company needs new business card

Our nearly 20 year old custom software development company would like to better include the fact that we are now providing Bitcoin services. These new services are B2B include education (how to acquire and securely hold Bitcoin) and integrating Bitcoin payments into existing ecommerce sites or other existing systems. Please keep the card clean and simple. Attached is our current design and some other files. vextorial.com

Target Market(s)

businesses owners interested in long term relationship

Industry/Entity Type

Custom software development and Bitcoin

Contact Information for Business Card

Dale Parker, dale@vextorial.com, vextorial.com, (888) 555-VXTRL

Font styles to use
Other font styles liked:
• monospace

Requirements
Must have
• double-sided
Nice to have
• clean and simple
Should not have
• physical address

```html
<!DOCTYPE html>
<html lang="en">
<head>
<meta charset="utf-8">
<title>Vextorial Business Card</title>
<link rel="stylesheet" href="https://fonts.googleapis.com/css2?family=Lato:wght@300;900&family=Roboto+Mono:wght@400;700&display=swap">
<style>
  :root {
    --stage: #5f5e5f;
    --brand-blue: #3d70b8;
    --brand-orange: #f07b22;
    --paper: #ffffff;
    --card-shadow: 0 3px 6px rgba(0,0,0,0.35);
  }
  html, body {
    margin: 0;
    padding: 0;
    width: 1200px;
    height: 1200px;
    overflow: hidden;
    background: var(--stage);
  }
  .card {
    position: absolute;
    left: 250px;
    width: 700px;
    height: 400px;
    box-shadow: var(--card-shadow);
    overflow: hidden;
  }
  .card-front { top: 170px; background: var(--paper); }
  .card-back { top: 630px; background: var(--brand-blue); }

  .brand {
    position: absolute;
    left: 0;
    width: 100%;
    display: flex;
    justify-content: center;
    align-items: center;
    gap: 14px;
  }
  .brand-mark {
    display: block;
    background: var(--brand-orange);
  }
  .brand-name {
    font-family: "Lato", sans-serif;
    font-weight: 900;
    text-transform: uppercase;
    letter-spacing: 1px;
    line-height: 1;
  }
  .tagline {
    position: absolute;
    left: 0;
    width: 100%;
    text-align: center;
    font-family: "Lato", sans-serif;
    font-weight: 300;
    letter-spacing: -1px;
    line-height: 1;
    margin: 0;
  }

  /* front */
  .card-front .brand { top: 92px; }
  .card-front .brand-mark { width: 40px; height: 40px; }
  .card-front .brand-name { font-size: 66px; color: var(--brand-blue); }
  .card-front .tagline { top: 164px; font-size: 24px; color: var(--brand-blue); }

  .contact-band {
    position: absolute;
    left: 0;
    top: 260px;
    width: 100%;
    height: 140px;
    background: var(--brand-blue);
  }
  .band-notch { position: absolute; left: 0; top: 260px; }
  .contact-list {
    position: absolute;
    left: 42px;
    top: 36px;
    margin: 0;
    padding: 0;
    list-style: none;
    font-family: "Roboto Mono", monospace;
    font-size: 16px;
    color: var(--paper);
  }
  .contact-list li {
    display: flex;
    align-items: center;
    gap: 10px;
    height: 24.5px;
  }
  .contact-list svg { width: 14px; height: 14px; flex: none; }
  .holder-name {
    position: absolute;
    right: 44px;
    top: 54px;
    margin: 0;
    font-family: "Roboto Mono", monospace;
    font-weight: 700;
    font-size: 29px;
    letter-spacing: 1px;
    color: var(--paper);
  }

  /* back */
  .card-back .brand { top: 124px; }
  .card-back .brand-mark { width: 52px; height: 52px; }
  .card-back .brand-name { font-size: 86px; color: var(--paper); }
  .card-back .tagline { top: 222px; font-size: 31px; color: var(--paper); }
  .services {
    position: absolute;
    left: 0;
    top: 324px;
    width: 100%;
    text-align: center;
    font-family: "Roboto Mono", monospace;
    font-size: 16px;
    line-height: 24px;
    color: var(--paper);
    margin: 0;
    text-transform: uppercase;
  }
  .services .sep {
    display: inline-block;
    width: 7px;
    height: 7px;
    background: var(--paper);
    vertical-align: 3px;
    margin: 0 4px;
  }
</style>
</head>
<body>
  <section class="card card-front">
    <div class="brand">
      <span class="brand-mark"></span>
      <span class="brand-name">Vextorial</span>
    </div>
    <p class="tagline">developer of custom applications</p>

    <div class="contact-band">
      <ul class="contact-list">
        <li>
          <svg viewBox="0 0 16 16" aria-hidden="true"><path fill="#fff" d="M3.5 1.5l2.4 2.6-1.3 1.8c.9 2 2.4 3.6 4.5 4.6l1.8-1.3 2.6 2.4-1.4 2.2C6.4 13.4 2.4 9.4 1.3 3z"/></svg>
          <span>(888) 555-VXTRL</span>
        </li>
        <li>
          <svg viewBox="0 0 16 16" aria-hidden="true"><rect x="1" y="3" width="14" height="10" fill="#fff"/><path d="M1 3l7 6 7-6" fill="none" stroke="#3d70b8" stroke-width="1.4"/></svg>
          <span>dale@vextorial.com</span>
        </li>
        <li>
          <svg viewBox="0 0 16 16" aria-hidden="true"><circle cx="8" cy="8" r="6.5" fill="none" stroke="#fff" stroke-width="1.6"/><path d="M1.5 8h13M8 1.5c-2.6 3.6-2.6 9.4 0 13M8 1.5c2.6 3.6 2.6 9.4 0 13" fill="none" stroke="#fff" stroke-width="1.2"/></svg>
          <span>vextorial.com</span>
        </li>
      </ul>
      <p class="holder-name">DALE PARKER</p>
    </div>
    <svg class="band-notch" width="700" height="40" viewBox="0 0 700 40" aria-hidden="true">
      <polygon points="558,0 606,0 550,32" fill="#ffffff"/>
    </svg>
  </section>

  <section class="card card-back">
    <div class="brand">
      <span class="brand-mark"></span>
      <span class="brand-name">Vextorial</span>
    </div>
    <p class="tagline">developer of custom applications</p>
    <p class="services">
      Web &amp; native applications<span class="sep"></span>digital process automation<br>
      Cloud-based portals<span class="sep"></span>bitcoin consulting
    </p>
  </section>
</body>
</html>
```